US company needs luxury product packaging design for a line of hair extensions

What we Need:
Design product packaging for our top of the line hair extension product called Verosina™, the design should have the Verosina™ name,and the head from our Dovetress logo on the box.

Who we are
Our company DoveTress™ is a wholesaler of 100% human hair extensions. We sell the best quality double drawn hair wefts, clip-ins and wigs.

The detailed brief is in the attached word document with examples of packaging we like and we have also uploaded our company logo

The winning designer(s) will work with us on 9 other products packages that we need, so it is important to think strategically

Thanks

Target Market(s)

African American Women

Industry/Entity Type

Hair And Beauty

Font styles to use
Serif
Decorative
Script

Colors
fbf289
b768aa
e24096
000000
fbd4d5
f59195
ffc214
d3a5cc
eda3c7

Requirements
Must have
• Evoke luxury
Nice to have
• See Attached brief

```html
<!DOCTYPE html>
<html lang="en">
<head>
<meta charset="utf-8">
<title>Avora Drawer Slider Rigid Box – Dieline Layout</title>
<link href="https://fonts.googleapis.com/css2?family=Roboto:wght@400&family=Playfair+Display:ital,wght@0,400;1,400&display=swap" rel="stylesheet">
<style>
  :root {
    --canvas: #b3b3b3;
    --ink: #1a1a1a;
    --purple: #5c0080;
    --purple-deep: #2a0840;
    --night: #050008;
    --gold: #ffc214;
    --pink: #e24096;
    --berry: #a0145a;
    --white: #ffffff;
    --tray-rim: #555555;
    --soft-white: #f2f2f2;
  }
  html, body {
    margin: 0;
    padding: 0;
    width: 1200px;
    height: 1200px;
    overflow: hidden;
    background: var(--canvas);
  }
  .sheet { display: block; width: 1200px; height: 1200px; }
  .spec-title { font-family: "Roboto", sans-serif; font-size: 14px; fill: var(--ink); }
  .spec-line { font-family: "Roboto", sans-serif; font-size: 10.5px; fill: var(--ink); }
  .brand { font-family: "Playfair Display", serif; font-weight: 400; letter-spacing: 2px; }
  .brand-gold { fill: var(--gold); }
  .brand-white { fill: var(--soft-white); }
  .tagline { font-family: "Playfair Display", serif; font-style: italic; fill: var(--gold); }
  .fine { font-family: "Roboto", sans-serif; }
  .fine-dark { fill: #333333; }
  .fine-light { fill: #d9c9e6; }
  .caps { font-family: "Roboto", sans-serif; letter-spacing: 0.3px; }
</style>
</head>
<body>
<svg class="sheet" viewBox="0 0 1200 1200" xmlns="http://www.w3.org/2000/svg">
  <defs>
    <linearGradient id="drawer-vertical" x1="0" y1="0" x2="0" y2="1">
      <stop offset="0" stop-color="var(--night)"/>
      <stop offset="0.22" stop-color="var(--purple)"/>
      <stop offset="0.78" stop-color="var(--purple)"/>
      <stop offset="1" stop-color="var(--night)"/>
    </linearGradient>
    <linearGradient id="flap-left" x1="0" y1="0" x2="1" y2="0">
      <stop offset="0" stop-color="var(--night)"/>
      <stop offset="1" stop-color="var(--purple)"/>
    </linearGradient>
    <linearGradient id="flap-right" x1="1" y1="0" x2="0" y2="0">
      <stop offset="0" stop-color="var(--night)"/>
      <stop offset="1" stop-color="var(--purple)"/>
    </linearGradient>
    <linearGradient id="sleeve-top" x1="0" y1="0" x2="0" y2="1">
      <stop offset="0" stop-color="var(--purple-deep)"/>
      <stop offset="1" stop-color="var(--night)"/>
    </linearGradient>
    <linearGradient id="sleeve-bottom" x1="0" y1="0" x2="0" y2="1">
      <stop offset="0" stop-color="var(--night)"/>
      <stop offset="1" stop-color="var(--purple-deep)"/>
    </linearGradient>
    <linearGradient id="sleeve-band" x1="0" y1="0" x2="0" y2="1">
      <stop offset="0" stop-color="var(--night)"/>
      <stop offset="1" stop-color="var(--purple-deep)"/>
    </linearGradient>
    <radialGradient id="portrait-fill" cx="0.5" cy="0.45" r="0.6">
      <stop offset="0" stop-color="var(--pink)"/>
      <stop offset="1" stop-color="var(--berry)"/>
    </radialGradient>
  </defs>

  <!-- Specification block -->
  <g class="spec-block">
    <text class="spec-title" x="31" y="211">DRAWER SLIDER RIGID BOX</text>
    <text class="spec-line" x="31" y="226">CUSTOMER:  MERIDA2020</text>
    <text class="spec-line" x="31" y="268">DATE COMPLETED:  14 SEPT 2016</text>
    <text class="spec-line" x="31" y="281">STYLE:  CUSTOM RIGID BOX</text>
    <text class="spec-line" x="31" y="294">SIZE:  DRAWER - 10" X 8" X 3"</text>
    <text class="spec-line" x="31" y="309">SLEEVE - 10.125" X 3.125" X 8.125"</text>
    <text class="spec-line" x="31" y="324">MATERIAL:  .060 GAUGE PAPERBOARD THICKNESS</text>
  </g>

  <!-- Drawer outer wrap -->
  <g class="drawer-outer">
    <rect x="388" y="331" width="70" height="185" fill="url(#flap-left)"/>
    <rect x="638" y="331" width="70" height="185" fill="url(#flap-right)"/>
    <rect x="458" y="274" width="180" height="299" fill="url(#drawer-vertical)"/>
    <polygon points="458,331 458,347 453,331" fill="var(--canvas)"/>
    <polygon points="638,331 638,347 643,331" fill="var(--canvas)"/>
    <polygon points="458,516 458,500 453,516" fill="var(--canvas)"/>
    <polygon points="638,516 638,500 643,516" fill="var(--canvas)"/>
  </g>

  <!-- Drawer inner liner -->
  <g class="drawer-liner">
    <rect x="834" y="295" width="180" height="27" fill="var(--purple-deep)"/>
    <rect x="834" y="322" width="180" height="26" fill="var(--white)"/>
    <rect x="834" y="500" width="180" height="26" fill="var(--white)"/>
    <rect x="834" y="526" width="180" height="26" fill="var(--purple-deep)"/>
    <rect x="785" y="348" width="25" height="152" fill="var(--purple-deep)"/>
    <rect x="810" y="348" width="24" height="152" fill="var(--white)"/>
    <rect x="1014" y="348" width="24" height="152" fill="var(--white)"/>
    <rect x="1038" y="348" width="25" height="152" fill="var(--purple-deep)"/>
    <rect x="834" y="348" width="180" height="152" fill="var(--tray-rim)"/>
    <rect x="837" y="351" width="174" height="146" rx="6" fill="var(--white)"/>

    <g class="liner-copy" transform="rotate(180 924 380)">
      <text class="caps fine-dark" x="924" y="364" font-size="4" text-anchor="middle">ABOUT VEROSINA</text>
      <line x1="874" y1="367" x2="974" y2="367" stroke="#888" stroke-width="0.4"/>
      <text class="fine fine-dark" font-size="3.6" text-anchor="middle">
        <tspan x="924" y="373">Verosina™ is an ultra-luxurious 100% human</tspan>
        <tspan x="924" y="378">hair extension with all the cuticles intact.</tspan>
        <tspan x="924" y="383">Each bundle is carefully sorted, gently</tspan>
        <tspan x="924" y="388">steamed and hand finished by our in-house team.</tspan>
      </text>
      <line x1="874" y1="394" x2="974" y2="394" stroke="#888" stroke-width="0.4"/>
    </g>

    <g class="liner-copy">
      <text class="caps fine-dark" x="924" y="448" font-size="4" text-anchor="middle">ABOUT VEROSINA</text>
      <line x1="874" y1="451" x2="974" y2="451" stroke="#888" stroke-width="0.4"/>
      <text class="fine fine-dark" font-size="3.6" text-anchor="middle">
        <tspan x="924" y="458">Verosina™ is an ultra-luxurious 100% human</tspan>
        <tspan x="924" y="463">hair extension with all the cuticles intact.</tspan>
        <tspan x="924" y="468">Each bundle is carefully sorted, gently</tspan>
        <tspan x="924" y="473">steamed and hand finished by our in-house team.</tspan>
      </text>
      <line x1="874" y1="486" x2="974" y2="486" stroke="#888" stroke-width="0.4"/>
    </g>
  </g>

  <!-- Sleeve wrap -->
  <g class="sleeve">
    <rect x="210" y="654" width="204" height="165" fill="url(#sleeve-top)"/>
    <rect x="64" y="820" width="157" height="59" fill="url(#sleeve-band)"/>
    <rect x="221" y="819" width="182" height="60" fill="url(#sleeve-band)"/>
    <rect x="403" y="820" width="157" height="59" fill="url(#sleeve-band)"/>
    <rect x="210" y="879" width="204" height="167" fill="url(#sleeve-bottom)"/>

    <rect class="sleeve-back-frame" x="224" y="668" width="176" height="149" fill="none" stroke="#6f5a80" stroke-width="0.6"/>
    <g class="sleeve-back" transform="rotate(180 312 736)">
      <text class="brand brand-white" x="312" y="731" font-size="17" text-anchor="middle">AVORA</text>
      <text class="caps fine-light" x="312" y="742" font-size="3.6" text-anchor="middle">100% HUMAN HAIR EXTENSIONS</text>
      <line x1="262" y1="768" x2="362" y2="768" stroke="#8b7a99" stroke-width="0.4"/>
      <text class="fine fine-light" font-size="3.4" text-anchor="middle">
        <tspan x="312" y="777">Product of DoveTress LLC. All rights reserved. DoveTress logo</tspan>
        <tspan x="312" y="782">is a trademark of DoveTress, registered in the USA.</tspan>
      </text>
      <line x1="262" y1="790" x2="362" y2="790" stroke="#8b7a99" stroke-width="0.4"/>
    </g>

    <g class="sleeve-side" transform="rotate(180 162 849)">
      <text class="brand brand-gold" x="162" y="850" font-size="17" text-anchor="middle">AVORA</text>
      <text class="tagline" x="162" y="861" font-size="4.5" text-anchor="middle">100% Human Hair Extensions</text>
      <circle cx="236" cy="838" r="5" fill="#6f5a80"/>
    </g>
    <g class="sleeve-side" transform="rotate(180 462 849)">
      <text class="brand brand-gold" x="462" y="850" font-size="17" text-anchor="middle">AVORA</text>
      <text class="tagline" x="462" y="861" font-size="4.5" text-anchor="middle">100% Human Hair Extensions</text>
      <circle cx="536" cy="838" r="5" fill="#6f5a80"/>
    </g>

    <g class="sleeve-front">
      <ellipse role="img" aria-label="Illustration of a woman's profile framed by flowing glittering pink hair" cx="320" cy="950" rx="47" ry="58" fill="url(#portrait-fill)"/>
      <text class="brand brand-gold" x="312" y="1000" font-size="18" text-anchor="middle">AVORA</text>
      <text class="tagline" x="312" y="1011" font-size="4.5" text-anchor="middle">100% Human Hair Extensions</text>
      <line x1="262" y1="1021" x2="362" y2="1021" stroke="#6f5a80" stroke-width="0.5"/>
    </g>
  </g>

  <!-- Sleeve liner (unprinted) -->
  <g class="sleeve-liner">
    <text class="brand brand-white" x="929" y="650" font-size="16" text-anchor="middle">AVORA</text>
    <text class="caps" x="929" y="658" font-size="3.6" fill="#dddddd" text-anchor="middle">100% HUMAN HAIR EXTENSIONS</text>
    <rect x="806" y="674" width="182" height="359" fill="var(--white)"/>
    <rect x="664" y="823" width="466" height="61" fill="var(--white)"/>
  </g>
</svg>
</body>
</html>
```